Wordpress Design (uncoded) Auction & Real Estate 3 in 1

This will be an uncoded Wordpress theme design only. Winning designer will provide PSD source files.

We need a wordpress themedesign for an established auction and real estate company based in Pennsylvania. The client wants one overall theme for their primary company website with 2 child themes, one for auction division and one for real estate division. Each child theme will have it's own color scheme and some variation in layout.

The primary company logo is Blue with white/black/silver elements. (see attached zip file)

The auction division logo is Gold with black/white elements (see attached zip file)

The real estate division logo is Green with white/black/silver elements. (see attached zip file)

Also attached are 2 PDF files showing a sample layout that the client came up with that they really like; however, this should only be used as a starting point. We want to see what creative, clean layouts you can come up with.

Industry/Entity Type

Real Estate

Requirements
Must have
• - We will require winning designer to provide a layered PSD (Adobe photoshop) concept files, along with any non-standard font files used.

A slideshow element on the home page using the placeholder image provided.

Primary Site navigation for merrowtonhalvecompanies.example:

Home
Services
-Auctions/Appraisals
-Real Estate Auctions
-Real Estate Listings
About Us
-History
-Auction Center
Contact Us

Secondary site - halvegavelhouse.example navigation:
Home
Auctions
Buy/Sell
Collections
Services
Contact Us

Secondary site - merrowtonhalve.example
Home
Properties
Real Estate Auctions
Buying
Selling
Area Info
About Us
Contact Us
Nice to have
• Sidebar widgets: Email sign-up form - Featured Auctions - Featured Assets for Sale

```html
<!DOCTYPE html>
<html lang="en">
<head>
<meta charset="utf-8">
<title>Merrowton Halve Real Estate</title>
<link href="https://fonts.googleapis.com/css2?family=Signika:wght@400;600&family=Arimo:ital,wght@0,400;0,700;1,400&display=swap" rel="stylesheet">
<style>
:root{
  --green:#1f6b45;
  --green-dark:#0f4f31;
  --green-light:#3f8f5f;
  --brown:#2a0e08;
  --brown-light:#6a3a2c;
  --text:#1c1c1c;
  --muted:#555;
  --gray:#7a7a7a;
  --panel:#f4f4f4;
  --line:#d9d9d9;
  --olive:#6b5f45;
}
*{box-sizing:border-box;margin:0;padding:0}
html,body{width:960px;height:1200px;overflow:hidden;background:#fff}
body{position:relative;font-family:"Arimo",Arial,sans-serif;color:var(--text)}
.abs{position:absolute}
.top-rule{left:0;top:0;width:960px;height:4px;background:var(--green)}
.brand{left:83px;top:44px;display:flex;align-items:center;gap:10px}
.brand-dot{width:40px;height:40px;border-radius:50%;background:var(--green)}
.brand-name{font-family:"Signika",sans-serif;font-weight:600;font-size:24px;color:var(--green);line-height:1}
.search{left:674px;top:18px;width:195px;height:31px;border:1px solid #ccc;border-radius:16px;background:linear-gradient(#fafafa,#ececec);font-size:11px;color:#aaa;padding:9px 12px}
.search svg{position:absolute;right:12px;top:8px}
.nav-item{top:119px;height:29px;border-radius:6px;background:linear-gradient(var(--green-light),var(--green-dark));color:#fff;font-size:11.5px;display:flex;align-items:center;justify-content:center;box-shadow:0 2px 3px rgba(0,0,0,.25)}
.nav-item::after{content:"";position:absolute;left:50%;bottom:-7px;margin-left:-8px;border:8px solid transparent;border-bottom:0;border-top:7px solid #2c6f49}
.slider{left:82px;top:184px;width:528px;height:294px;border:1px solid #e2e2e2;border-radius:8px;background:#fff;box-shadow:0 0 5px rgba(0,0,0,.12)}
.slide-photo{position:absolute;left:10px;top:10px;width:507px;height:272px;background:linear-gradient(#9fc4e6 0%,#cfe1f1 40%,#c6cbcf 58%,#8c8478 75%,#5b4d41 100%)}
.signup{left:630px;top:184px;width:250px;height:294px;border:1px solid #e2e2e2;border-radius:8px;background:linear-gradient(#f2f2f2,#fbfbfb);box-shadow:0 0 5px rgba(0,0,0,.12);overflow:hidden}
.signup-corner{position:absolute;right:0;top:0}
.signup h2{position:absolute;left:11px;top:20px;font-family:"Signika",sans-serif;font-weight:600;font-size:21px;color:#555}
.signup h2 span{color:var(--green)}
.signup p{position:absolute;left:12px;top:53px;width:226px;font-size:9.5px;line-height:14px;color:#333;letter-spacing:.3px;text-align:justify}
.field{position:absolute;left:12px;width:225px;height:34px;border:1px solid #ddd;border-radius:17px;background:#efefef;box-shadow:inset 0 2px 3px rgba(0,0,0,.08);font-size:10.5px;color:#444;padding:10px 15px}
.subscribe{position:absolute;left:114px;top:245px;width:121px;height:35px;border-radius:7px;background:linear-gradient(var(--green-light),var(--green-dark));color:#fff;font-family:"Signika",sans-serif;font-size:14px;display:flex;align-items:center;justify-content:center;border:2px solid #e6efe9;box-shadow:0 0 0 1px var(--green-dark)}
.intro-title{left:0;width:917px;top:506px;text-align:center;font-family:"Signika",sans-serif;font-weight:600;font-size:21px;color:#333;letter-spacing:.5px}
.intro-text{left:90px;width:786px;top:543px;text-align:center;font-size:9.7px;line-height:16px;color:#222}
.section-rule{left:40px;top:624px;width:850px;height:2px;background:linear-gradient(90deg,transparent,#e6e6e6 15%,#e6e6e6 85%,transparent)}
.col-rule{left:621px;top:648px;width:2px;height:410px;background:linear-gradient(transparent,#e4e4e4 10%,#e4e4e4 90%,transparent)}
.h-col{font-family:"Signika",sans-serif;font-weight:600;font-size:16.5px;color:#333;letter-spacing:.4px}
.item-title{font-family:"Signika",sans-serif;font-weight:600;font-size:12px;color:var(--green);letter-spacing:.3px}
.thumb{width:112px;height:75px;background:linear-gradient(#9cc1de 0%,#b6c9a0 45%,#7aa65a 70%,#5f9a3f 100%)}
.live{font-family:"Signika",sans-serif;font-weight:600;font-size:11px;color:var(--olive);letter-spacing:.6px}
.meta{font-size:9px;font-style:italic;line-height:11px;color:#333}
.meta b{font-weight:700}
.btn{height:21px;border-radius:11px;color:#fff;font-size:9.5px;display:flex;align-items:center;justify-content:center;gap:6px;border:2px solid #e8e8e8;box-shadow:0 0 0 1px #333}
.btn-green{background:linear-gradient(var(--green-light),var(--green-dark));box-shadow:0 0 0 1px var(--green-dark)}
.btn-brown{background:linear-gradient(var(--brown-light),var(--brown))}
.btn-read{font-style:italic}
.dotted{height:0;border-top:1px dotted #bbb}
.link{font-size:9.5px;color:var(--green);text-decoration:underline;letter-spacing:.5px}
.side-text{font-size:9px;line-height:11.5px;color:#222}
.side-photo{border:1px solid #ddd;padding:2px;background:#fff}
.side-photo div{width:100%;height:100%}
.foot-band{left:0;top:1078px;width:960px;height:8px;background:var(--green)}
.foot-mark{left:106px;top:1100px;width:54px;height:68px;border:2px solid #333;border-radius:50%}
.foot-head{top:1105px;font-size:10.5px;color:#444;letter-spacing:.3px}
.foot-link{font-size:9.5px;color:#444;line-height:16px}
.foot-link li{list-style:none}
.foot-link li::before{content:"»";font-size:8px;margin-right:4px}
.foot-line{top:1180px;font-size:9.5px;color:#444}
</style>
</head>
<body>
<div class="abs top-rule"></div>

<header>
  <div class="abs brand"><span class="brand-dot"></span><span class="brand-name">Merrowton Halve Real Estate</span></div>
  <div class="abs search">search
    <svg width="14" height="14" viewBox="0 0 14 14"><circle cx="6" cy="6" r="4.2" fill="none" stroke="#1aa04a" stroke-width="2.2"/><line x1="9" y1="9" x2="12.5" y2="12.5" stroke="#1aa04a" stroke-width="2.4" stroke-linecap="round"/></svg>
  </div>
  <nav>
    <div class="abs nav-item" style="left:383px;width:67px">HOME</div>
    <div class="abs nav-item" style="left:465px;width:81px">ABOUT US</div>
    <div class="abs nav-item" style="left:564px;width:82px">HISTORY</div>
    <div class="abs nav-item" style="left:663px;width:112px">AUCTION CENTER</div>
    <div class="abs nav-item" style="left:792px;width:83px">CONTACT US</div>
  </nav>
</header>

<section class="abs slider">
  <div class="slide-photo" role="img" aria-label="Slideshow photo: auction center building with bare trees and parking lot under blue sky"></div>
</section>

<aside class="abs signup">
  <svg class="signup-corner" width="125" height="48" viewBox="0 0 125 48"><path d="M0 0H125V34C95 26 72 32 60 46C52 26 30 8 0 0Z" fill="#1f7a4a"/><path d="M0 0C30 8 52 26 60 46C50 34 30 22 8 12Z" fill="#e3e3e3"/></svg>
  <h2>Email <span>sign-up</span> form</h2>
  <p>Lorem ipsum dolor sit amet, consectetuer adipiscing elit. Nam</p>
  <div class="field" style="top:102px">First Name</div>
  <div class="field" style="top:147px">Last Name</div>
  <div class="field" style="top:192px">Email Address</div>
  <div class="subscribe">Subscribe Now</div>
</aside>

<h1 class="abs intro-title">More Choices... More Solutions</h1>
<p class="abs intro-text">A family business since 1959, Merrowton Halve Companies offer honest, professional, and personal service. This early commitment to service and the motto "People Serving People" continues today. Our breadth of services allows us to be a true partner, providing you with comprehensive support and solutions for all areas of your transition ...we're able to help you buy it, sell it, move it, and store it.</p>

<div class="abs section-rule"></div>
<div class="abs col-rule"></div>

<main>
  <h2 class="abs h-col" style="left:95px;top:659px">Shop Equipment/tools * Pork Processing Items</h2>

  <h3 class="abs item-title" style="left:101px;top:690px">Incredible Home in Cedar Bend' exclusive Highview Lake community</h3>
  <div class="abs thumb" style="left:98px;top:714px" role="img" aria-label="Photo of a home with palm trees and lawn"></div>
  <div class="abs live" style="left:219px;top:712px">LIVE ON-SITE AUCTION</div>
  <div class="abs meta" style="left:218px;top:732px"><b>Begins:</b>&nbsp; Tuesday, April 23, 2013 at 10:00 AM EDT</div>
  <div class="abs meta" style="left:218px;top:754px"><b>Location:</b>&nbsp; Highview Lake Entrance- 1400 N. Ridge Hwy 7<br>Highview Lake Rd (Auction Property)<br>Cedar Bend, FL 33000</div>
  <div class="abs btn btn-green" style="left:101px;top:804px;width:98px"><svg width="12" height="10" viewBox="0 0 12 10"><rect x="0.5" y="0.5" width="3" height="9" fill="none" stroke="#fff"/><path d="M6 2H12M6 5H12M6 8H12" stroke="#fff"/></svg>Details Now</div>
  <div class="abs btn btn-brown" style="left:216px;top:804px;width:99px"><svg width="12" height="10" viewBox="0 0 12 10"><rect x="0.5" y="0.5" width="11" height="9" fill="none" stroke="#fff"/><path d="M2 8L5 4L7 6L9 3L11 8Z" fill="#fff"/></svg>Details Now</div>

  <div class="abs dotted" style="left:84px;top:853px;width:526px"></div>

  <h3 class="abs item-title" style="left:97px;top:882px">Incredible Home in Cedar Bend' exclusive Highview Lake community</h3>
  <div class="abs thumb" style="left:98px;top:914px" role="img" aria-label="Photo of a home with palm trees and lawn"></div>
  <div class="abs live" style="left:218px;top:911px">LIVE ON-SITE AUCTION</div>
  <div class="abs meta" style="left:218px;top:931px"><b>Begins:</b>&nbsp; Tuesday, April 23, 2013 at 10:00 AM EDT</div>
  <div class="abs meta" style="left:218px;top:953px"><b>Location:</b>&nbsp; Highview Lake Entrance- 1400 N. Ridge Hwy 7<br>Highview Lake Rd (Auction Property)<br>Cedar Bend, FL 33000</div>
  <div class="abs btn btn-green" style="left:101px;top:1003px;width:98px"><svg width="12" height="10" viewBox="0 0 12 10"><rect x="0.5" y="0.5" width="3" height="9" fill="none" stroke="#fff"/><path d="M6 2H12M6 5H12M6 8H12" stroke="#fff"/></svg>Details Now</div>
  <div class="abs btn btn-brown" style="left:216px;top:1003px;width:99px"><svg width="12" height="10" viewBox="0 0 12 10"><rect x="0.5" y="0.5" width="11" height="9" fill="none" stroke="#fff"/><path d="M2 8L5 4L7 6L9 3L11 8Z" fill="#fff"/></svg>Details Now</div>
</main>

<aside>
  <h2 class="abs h-col" style="left:640px;top:659px">Featured Auctions</h2>
  <a class="abs link" style="left:641px;top:692px">TRACTOR * HI LIFT * MACHINERY</a>
  <div class="abs side-text" style="left:641px;top:726px;width:100px"><b>Saturday</b> March 16, 2013 at 10:00 AM</div>
  <div class="abs side-text" style="left:641px;top:754px;width:100px">simply dummy text of the printing and type-setting industry.</div>
  <div class="abs side-photo" style="left:754px;top:714px;width:103px;height:106px"><div role="img" aria-label="Photo of hands holding a small model house" style="background:linear-gradient(#2a2a2a,#5a4a44 50%,#d9a67c 75%,#c98d63)"></div></div>
  <div class="abs btn btn-brown btn-read" style="left:651px;top:801px;width:74px">Read more</div>

  <div class="abs dotted" style="left:638px;top:854px;width:228px"></div>

  <h2 class="abs h-col" style="left:638px;top:864px">Featured Assets for Sale</h2>
  <div class="abs side-photo" style="left:637px;top:896px;width:235px;height:82px"><div role="img" aria-label="Photo of a two-story house with garage and trees" style="background:linear-gradient(#8fb6e4 0%,#b7cbe0 35%,#c9b394 60%,#8d8a6a 85%,#6d7b4c 100%)"></div></div>
  <p class="abs side-text" style="left:638px;top:988px;width:230px;font-size:9.5px;line-height:14.5px">A family business since 1959, Merrowton Halve Companies offer honest, professional, and per-sonal service. This early commitment....</p>
  <div class="abs btn btn-brown btn-read" style="left:798px;top:1041px;width:74px">Read more</div>
</aside>

<footer>
  <div class="abs foot-band"></div>
  <div class="abs foot-mark"></div>
  <div class="abs foot-head" style="left:275px">HOME</div>
  <div class="abs foot-head" style="left:361px">SERVICES</div>
  <ul class="abs foot-link" style="left:361px;top:1123px"><li>Auction</li><li>Real Estate</li><li>BIDLINE</li></ul>
  <div class="abs foot-head" style="left:468px">ABOUT US</div>
  <ul class="abs foot-link" style="left:468px;top:1123px"><li>History</li><li>Auction Center</li></ul>
  <div class="abs foot-head" style="left:577px">CONTACT US</div>
  <ul class="abs foot-link" style="left:577px;top:1123px"><li>Privacy</li><li></li></ul>
  <div class="abs foot-line" style="left:110px">215 555 0142</div>
  <div class="abs foot-line" style="left:207px">88 Orchard Mill Road , Quakerfield, PA 19000</div>
  <div class="abs foot-line" style="left:674px;top:1182px">(C) 2013 The Merrowton Halve Companies</div>
</footer>
</body>
</html>
```